Rancher Pell Pet Packaging and Tag Design

Create a design for a label card to attach and hang leather pet toys on in merchandise displays. Card will be of a heavy cardboard stock. The design should be simple with a maximum of 4 colors. We would like for it to be whimsical or cartoonish in nature. The focus of the product line will be directed to Farm and Ranch locations that carry Pet supplies. The leather toys will range from leather shaped farm animals to wildlife animals. They could include chewables such as bones or rope type toys. We are a canadian company who are proud of our heritage. The typical card size will be typically 4-6" wide and 8-10" tall. A caricature of Rancher Pell could become the main company logo
Updates
Target Market(s)
Farm and Ranch shoppers for Pet Toys
Industry/Entity Type
Pet and Farm
Look and feel
Each slider illustrates characteristics of the customer's brand and the style your logo design should communicate.

```html
<!DOCTYPE html>
<html lang="en">
<head>
<meta charset="utf-8">
<title>Rancher Pell Leather Toys – Hang Tags</title>
<link rel="stylesheet" href="https://fonts.googleapis.com/css2?family=Oswald:wght@500;700&display=swap">
<style>
  :root {
    --page-bg: #e4e2df;
    --leather-rim: #8e3a1a;
    --leather-rim-dark: #6d2a10;
    --stitch: #c9774a;
    --panel-light: #e0b077;
    --panel-mid: #c98a4f;
    --panel-edge: #a8662f;
    --ink: #1e1008;
    --logo-ink: #3a1f12;
    --art-light: #d7a46a;
    --art-dark: #8a5a30;
  }
  * { margin: 0; padding: 0; box-sizing: border-box; }
  html, body { width: 1200px; height: 875px; overflow: hidden; }
  body {
    background: var(--page-bg);
    font-family: "Oswald", "Arial Narrow", sans-serif;
    display: flex;
    align-items: center;
    justify-content: center;
    gap: 60px;
  }
  .hang-tag {
    position: relative;
    width: 456px;
    height: 760px;
  }
  .tag-shape {
    position: absolute;
    inset: 0;
    width: 100%;
    height: 100%;
  }
  .tag-content {
    position: absolute;
    inset: 0;
    text-align: center;
    color: var(--ink);
  }
  .origin-badge {
    position: absolute;
    left: 290px;
    top: 70px;
    width: 88px;
    height: 74px;
    border-radius: 50%;
    background: rgba(236, 200, 160, 0.55);
    transform: rotate(-12deg);
  }
  .brand-mark {
    position: absolute;
    left: 0;
    right: 0;
    top: 120px;
    display: flex;
    flex-direction: column;
    align-items: center;
    gap: 14px;
  }
  .brand-dot {
    width: 64px;
    height: 64px;
    border-radius: 50%;
    background: var(--logo-ink);
  }
  .brand-name {
    font-weight: 700;
    font-size: 46px;
    letter-spacing: 2px;
    line-height: 1;
    color: var(--logo-ink);
    text-transform: uppercase;
  }
  .product-line {
    position: absolute;
    left: 0;
    right: 0;
    top: 298px;
    line-height: 1;
    text-transform: uppercase;
  }
  .product-line .line-kicker {
    display: block;
    font-weight: 500;
    font-size: 27px;
    letter-spacing: 3px;
  }
  .product-line .line-title {
    display: block;
    font-weight: 700;
    font-size: 46px;
    letter-spacing: 0;
    margin-top: 4px;
  }
  .dog-portrait {
    position: absolute;
    left: 68px;
    top: 378px;
    width: 312px;
    height: 300px;
    border-radius: 46% 46% 18% 18%;
    background: radial-gradient(ellipse at 50% 45%, var(--art-light) 0%, var(--art-dark) 100%);
    opacity: 0.75;
  }
  .feature-list {
    position: absolute;
    left: 0;
    right: 0;
    top: 680px;
    display: flex;
    justify-content: center;
    gap: 24px;
    list-style: none;
    font-weight: 500;
    font-size: 25px;
    line-height: 1;
    text-transform: uppercase;
  }
</style>
</head>
<body>

<svg width="0" height="0" style="position:absolute">
  <defs>
    <radialGradient id="panelGlow" cx="50%" cy="45%" r="65%">
      <stop offset="0%" stop-color="#e6b97f"/>
      <stop offset="60%" stop-color="#cf9156"/>
      <stop offset="100%" stop-color="#b06a32"/>
    </radialGradient>
  </defs>
</svg>

<article class="hang-tag">
  <svg class="tag-shape" viewBox="0 0 600 1000" preserveAspectRatio="none" aria-hidden="true">
    <path fill="var(--leather-rim)" d="M0,150 Q0,130 20,130 L120,130 C130,40 210,0 300,0 C390,0 470,40 480,130 L580,130 Q600,130 600,150 L600,980 Q600,1000 580,1000 L20,1000 Q0,1000 0,980 Z"/>
    <path fill="none" stroke="var(--stitch)" stroke-width="2" stroke-dasharray="6 5" d="M14,160 Q14,144 30,144 L132,144 C142,60 218,16 300,16 C382,16 458,60 468,144 L570,144 Q586,144 586,160 L586,972 Q586,986 570,986 L30,986 Q14,986 14,972 Z"/>
    <path fill="var(--panel-edge)" d="M36,180 L146,180 C156,96 226,54 300,54 C374,54 444,96 454,180 L564,180 L564,964 L36,964 Z"/>
    <path fill="url(#panelGlow)" d="M44,188 L152,188 C162,106 230,62 300,62 C370,62 438,106 448,188 L556,188 L556,956 L44,956 Z"/>
  </svg>
  <div class="tag-content">
    <div class="origin-badge" aria-hidden="true"></div>
    <div class="brand-mark">
      <span class="brand-dot" aria-hidden="true"></span>
      <span class="brand-name">Rancher Pell</span>
    </div>
    <h2 class="product-line">
      <span class="line-kicker">Chewables</span>
      <span class="line-title">Leathertoys</span>
    </h2>
    <div class="dog-portrait" role="img" aria-label="Engraved-style sketch of a droopy-eared hound's head"></div>
    <ul class="feature-list">
      <li>Durable</li>
      <li>Flevored</li>
      <li>Textured</li>
    </ul>
  </div>
</article>

<article class="hang-tag">
  <svg class="tag-shape" viewBox="0 0 600 1000" preserveAspectRatio="none" aria-hidden="true">
    <path fill="var(--leather-rim)" d="M0,150 Q0,130 20,130 L120,130 C130,40 210,0 300,0 C390,0 470,40 480,130 L580,130 Q600,130 600,150 L600,980 Q600,1000 580,1000 L20,1000 Q0,1000 0,980 Z"/>
    <path fill="none" stroke="var(--stitch)" stroke-width="2" stroke-dasharray="6 5" d="M14,160 Q14,144 30,144 L132,144 C142,60 218,16 300,16 C382,16 458,60 468,144 L570,144 Q586,144 586,160 L586,972 Q586,986 570,986 L30,986 Q14,986 14,972 Z"/>
    <path fill="var(--panel-edge)" d="M36,180 L146,180 C156,96 226,54 300,54 C374,54 444,96 454,180 L564,180 L564,964 L36,964 Z"/>
    <path fill="url(#panelGlow)" d="M44,188 L152,188 C162,106 230,62 300,62 C370,62 438,106 448,188 L556,188 L556,956 L44,956 Z"/>
  </svg>
  <div class="tag-content">
    <div class="origin-badge" aria-hidden="true"></div>
    <div class="brand-mark">
      <span class="brand-dot" aria-hidden="true"></span>
      <span class="brand-name">Rancher Pell</span>
    </div>
    <h2 class="product-line">
      <span class="line-kicker">Chewables</span>
      <span class="line-title">Leathertoys</span>
    </h2>
    <div class="dog-portrait" role="img" aria-label="Engraved-style sketch of a smiling short-haired terrier's head"></div>
    <ul class="feature-list">
      <li>Durable</li>
      <li>Flevored</li>
      <li>Textured</li>
    </ul>
  </div>
</article>

</body>
</html>
```